KRT Project Signage

Need a sign to be displayed in the front of properties currently under Construction or Renovation to advertise our company information. Need it to be Professional and Contemporary. We are a Design/Build Construction Company. Information should include Company Name, email, website, phone number. Attached: Logo and company brochure, also included and inspiration images

```html
<!DOCTYPE html>
<html lang="en">
<head>
<meta charset="utf-8">
<title>KRT Project Signage</title>
<link rel="stylesheet" href="https://fonts.googleapis.com/css2?family=Jost:wght@500;700&family=Poppins:wght@400;600;700&display=swap">
<style>
  :root {
    --backdrop: #bdbdbd;
    --sign-white: #ffffff;
    --brand-yellow: #f2ec46;
    --ink-navy: #0f1f26;
    --ink-dark: #222222;
    --band-black: #242424;
    --text-white: #ffffff;
  }
  * { box-sizing: border-box; margin: 0; padding: 0; }
  html, body {
    width: 800px; height: 1200px; overflow: hidden;
    background: var(--backdrop);
  }
  .canvas { position: relative; width: 800px; height: 1200px; }
  .sign {
    position: absolute; left: 70px; top: 105px;
    width: 660px; height: 990px;
    background: var(--sign-white);
    box-shadow: 8px 10px 12px rgba(0,0,0,0.35);
    overflow: hidden;
  }
  .name-panel {
    position: absolute; left: 62px; top: 0;
    width: 539px; height: 323px;
    background: var(--brand-yellow);
    border-radius: 0 0 78px 78px;
    text-align: center;
    color: var(--ink-navy);
  }
  .name-panel .person {
    font-family: 'Jost', sans-serif; font-weight: 700;
    font-size: 84px; line-height: 76px;
    padding-top: 80px; letter-spacing: -1px;
  }
  .name-panel .role {
    font-family: 'Jost', sans-serif; font-weight: 500;
    font-size: 28px; letter-spacing: 8px;
    margin-top: 8px; margin-left: 8px;
  }
  .contact {
    position: absolute; left: 62px; top: 362px;
    font-family: 'Poppins', sans-serif; font-weight: 400;
    font-size: 32px; line-height: 42px; color: var(--ink-dark);
  }
  .contact .row { display: flex; align-items: flex-start; }
  .contact .row + .row { margin-top: 12px; align-items: center; }
  .contact svg { flex: none; width: 34px; margin-right: 10px; }
  .contact .row:first-child svg { margin-top: 4px; }
  .phone-band {
    position: absolute; left: 0; top: 585px;
    width: 660px; height: 160px; background: var(--band-black);
  }
  .office-pill {
    position: absolute; left: 62px; top: 553px;
    width: 539px; height: 59px;
    background: var(--brand-yellow); border-radius: 30px;
    display: flex; align-items: center; padding-left: 7px;
    font-family: 'Poppins', sans-serif; font-weight: 700;
    white-space: nowrap;
  }
  .office-pill .label {
    background: var(--ink-navy); color: var(--text-white);
    border-radius: 24px; height: 46px; width: 184px;
    display: flex; align-items: center; justify-content: center;
    font-size: 31px;
  }
  .office-pill svg { flex: none; width: 44px; height: 44px; margin-left: 12px; }
  .office-pill .number {
    color: var(--ink-navy); font-size: 33px; letter-spacing: 2px;
    margin-left: 18px; line-height: 1;
  }
  .mobile {
    position: absolute; left: 62px; top: 626px; width: 539px;
    display: flex; align-items: center; white-space: nowrap;
  }
  .mobile svg { flex: none; width: 62px; height: 62px; }
  .mobile .number {
    font-family: 'Jost', sans-serif; font-weight: 700;
    font-size: 76px; line-height: 1; color: var(--text-white);
    margin-left: 10px; letter-spacing: -1px;
  }
  .company-mark {
    position: absolute; left: 0; top: 827px; width: 660px;
    display: flex; align-items: center; justify-content: center;
    font-family: 'Poppins', sans-serif; font-weight: 600;
    font-size: 34px; letter-spacing: 2px; color: var(--ink-dark);
  }
  .company-mark .dot {
    width: 52px; height: 52px; border-radius: 50%;
    background: var(--brand-yellow); margin-left: 16px;
  }
</style>
</head>
<body>
<main class="canvas">
  <section class="sign" aria-label="KRT construction project sign">
    <header class="name-panel">
      <h1 class="person">MARCUS<br>DELANE</h1>
      <p class="role">DESIGN &amp; BUILDER</p>
    </header>

    <div class="contact">
      <div class="row">
        <svg viewBox="0 0 24 32" aria-hidden="true"><path fill="#222" d="M12 0C5.4 0 0 5.2 0 11.7 0 20 12 32 12 32s12-12 12-20.3C24 5.2 18.6 0 12 0zm0 16.5a5 5 0 1 1 0-10 5 5 0 0 1 0 10z"/></svg>
        <p>1450 Harbor Line Rd., Ste. 310<br>Coral Vale, FL 33480</p>
      </div>
      <div class="row">
        <svg viewBox="0 0 32 24" aria-hidden="true"><rect x="1" y="2" width="30" height="20" fill="#222"/><path d="M1 2l15 12L31 2M1 22l11-10M31 22L20 12" stroke="#fff" stroke-width="1.8" fill="none"/></svg>
        <p>dana@krtconstruction.com</p>
      </div>
    </div>

    <div class="phone-band"></div>

    <div class="office-pill">
      <span class="label">OFFICE</span>
      <svg viewBox="0 0 48 48" aria-hidden="true">
        <circle cx="24" cy="24" r="24" fill="#0f1f26"/>
        <path fill="#f2ec46" d="M17 12c1-.6 2.2-.2 2.8.8l2.4 4.3c.5 1 .3 2.1-.6 2.8l-1.8 1.3c1 2.8 3.2 5.3 5.9 6.6l1.5-1.7c.7-.8 1.9-1 2.8-.4l4.1 2.7c1 .6 1.2 1.9.6 2.8l-1.5 2.3c-1 1.5-2.9 2.1-4.6 1.5C21 33 14.6 26.4 12.7 18.6c-.4-1.7.3-3.5 1.8-4.4z"/>
        <path d="M27 12a9 9 0 0 1 9 9M27 16.5a4.5 4.5 0 0 1 4.5 4.5" stroke="#f2ec46" stroke-width="2.2" fill="none" stroke-linecap="round"/>
      </svg>
      <span class="number">555.210.4830</span>
    </div>

    <div class="mobile">
      <svg viewBox="0 0 48 48" aria-hidden="true">
        <circle cx="24" cy="24" r="24" fill="#f2ec46"/>
        <path fill="#242424" d="M17 12c1-.6 2.2-.2 2.8.8l2.4 4.3c.5 1 .3 2.1-.6 2.8l-1.8 1.3c1 2.8 3.2 5.3 5.9 6.6l1.5-1.7c.7-.8 1.900-1 2.8-.4l4.1 2.7c1 .6 1.2 1.9.6 2.8l-1.5 2.3c-1 1.5-2.9 2.1-4.6 1.5C21 33 14.6 26.4 12.7 18.6c-.4-1.7.3-3.5 1.8-4.4z"/>
        <path d="M27 12a9 9 0 0 1 9 9M27 16.5a4.5 4.5 0 0 1 4.5 4.5" stroke="#242424" stroke-width="2.2" fill="none" stroke-linecap="round"/>
      </svg>
      <span class="number">555.318.2706</span>
    </div>

    <footer class="company-mark">
      <span>KRT CONSTRUCTION</span>
      <span class="dot" aria-hidden="true"></span>
    </footer>
  </section>
</main>
</body>
</html>
```